Business card for law firm

Need business card for new law firm. Think confident, authoritative, conservative, but not stuffy or old-fashioned.

Contact Information for Business Card

Content for card - logo (uploaded), plus the following:

Paul Whitcombe (larger font)
Managing Partner (larger font, but not as large as name)
Level 9, 7 Ferris Lane
Sydney NSW 2000
Main Tel 02 9364 2710
Direct Tel 02 8472 3159
Email paul@qvlegal.com.au
www.qvlegal.com.au

Letterhead design should include logo plus:
Level 9, 7 Ferris Lane
Sydney NSW 2000
Tel 02 8472 3159
www.qvlegal.com.au

```html
<!DOCTYPE html>
<html lang="en">
<head>
<meta charset="utf-8">
<title>Quayvale Lawyers – Business Card</title>
<link rel="stylesheet" href="https://fonts.googleapis.com/css2?family=Cormorant+Garamond:wght@500;600&display=swap">
<style>
  :root {
    --navy: #0b2277;
    --navy-deep: #081a5e;
    --ink: #1a1a1a;
    --grey: #6b6b6b;
    --rule: #d9d9de;
    --paper: #ffffff;
    --backdrop: #e9e8e4;
  }
  * { box-sizing: border-box; margin: 0; padding: 0; }
  html, body {
    width: 1200px; height: 768px; overflow: hidden;
    background: var(--backdrop);
    font-family: "Cormorant Garamond", "Times New Roman", serif;
  }
  .stage {
    width: 1200px; height: 768px;
    display: flex; align-items: center; justify-content: center; gap: 44px;
  }
  .card {
    width: 540px; height: 310px; position: relative; overflow: hidden;
    box-shadow: 0 8px 24px rgba(0,0,0,.18);
  }

  /* Front */
  .card-front { background: var(--paper); }
  .brand {
    position: absolute; left: 40px; top: 92px; width: 230px;
    display: flex; flex-direction: column; align-items: center;
  }
  .brand-mark { width: 34px; height: 34px; background: var(--navy); margin-bottom: 14px; }
  .brand-name {
    font-weight: 500; font-size: 38px; letter-spacing: 2px;
    color: var(--ink); line-height: 1;
  }
  .brand-tag {
    font-weight: 500; font-size: 11px; letter-spacing: 9px;
    color: var(--ink); margin-top: 8px; padding-left: 9px;
  }
  .divider {
    position: absolute; left: 292px; top: 34px; width: 1px; height: 196px;
    background: var(--rule);
  }
  .contact { position: absolute; left: 312px; top: 40px; right: 18px; }
  .contact-name {
    font-weight: 500; font-size: 23px; color: var(--navy);
    text-transform: uppercase; line-height: 1;
  }
  .contact-role {
    font-weight: 500; font-size: 13.5px; color: var(--ink);
    text-transform: uppercase; margin-top: 3px;
  }
  .contact-address {
    font-style: normal; font-size: 13px; color: var(--grey);
    line-height: 1.35; margin-top: 14px;
  }
  .contact-lines { list-style: none; margin-top: 10px; }
  .contact-lines li {
    display: flex; align-items: center; gap: 7px;
    font-size: 13px; color: var(--grey); line-height: 1.45;
  }
  .icon { width: 13px; height: 13px; flex: none; }

  .edge-rule {
    position: absolute; left: 0; bottom: 16px; width: 312px; height: 3px;
    background: var(--ink);
  }
  .edge-band {
    position: absolute; left: 0; bottom: 0; width: 100%; height: 36px;
  }
  .web {
    position: absolute; right: 20px; bottom: 9px;
    font-size: 13px; letter-spacing: 3px; color: var(--paper);
  }

  /* Back */
  .card-back { background: var(--navy-deep); }
  .back-brand {
    position: absolute; right: 40px; bottom: 40px;
    display: flex; align-items: center; gap: 12px;
  }
  .back-brand .brand-mark { width: 22px; height: 22px; background: var(--paper); margin: 0; }
  .back-brand .brand-name { color: var(--paper); font-size: 26px; }
</style>
</head>
<body>
<main class="stage">
  <section class="card card-front" aria-label="Card front">
    <div class="brand">
      <span class="brand-mark"></span>
      <span class="brand-name">QUAYVALE</span>
      <span class="brand-tag">LAWYERS</span>
    </div>
    <div class="divider"></div>
    <div class="contact">
      <h1 class="contact-name">Paul Whitcombe</h1>
      <p class="contact-role">Managing Partner</p>
      <address class="contact-address">Level 9, 7 Ferris Lane<br>Sydney NSW 2000</address>
      <ul class="contact-lines">
        <li>
          <svg class="icon" viewBox="0 0 13 13"><rect width="13" height="13" fill="#0b2277"/><path d="M3.5 3.2c.4-.4.9-.4 1.2 0l.8 1c.3.3.2.7-.1 1l-.4.4c.4.9 1.1 1.6 2 2l.4-.4c.3-.3.7-.4 1-.1l1 .8c.4.3.4.8 0 1.2l-.5.5C7.6 10 3 5.4 3.1 4z" fill="#fff"/></svg>
          02 9364 2710
        </li>
        <li>
          <svg class="icon" viewBox="0 0 13 13"><rect width="13" height="13" fill="#0b2277"/><path d="M3.5 3.2c.4-.4.9-.4 1.2 0l.8 1c.3.3.2.7-.1 1l-.4.4c.4.9 1.1 1.6 2 2l.4-.4c.3-.3.7-.4 1-.1l1 .8c.4.3.4.8 0 1.2l-.5.5C7.6 10 3 5.4 3.1 4z" fill="#fff"/></svg>
          02 8472 3159
        </li>
        <li>
          <svg class="icon" viewBox="0 0 13 13"><rect width="13" height="13" fill="#0b2277"/><rect x="3" y="4" width="7" height="5" fill="none" stroke="#fff" stroke-width="1"/><path d="M3 4l3.5 3L10 4" fill="none" stroke="#fff" stroke-width="1"/></svg>
          paul@qvlegal.com.au
        </li>
      </ul>
    </div>
    <div class="edge-rule"></div>
    <svg class="edge-band" viewBox="0 0 540 36" preserveAspectRatio="none" aria-hidden="true">
      <polygon points="0,28 312,28 326,0 540,0 540,36 0,36" fill="#0b2277"/>
    </svg>
    <span class="web">www.qvlegal.com.au</span>
  </section>

  <section class="card card-back" aria-label="Card back">
    <div class="back-brand">
      <span class="brand-mark"></span>
      <span class="brand-name">QUAYVALE</span>
    </div>
  </section>
</main>
</body>
</html>
```